Need a new company business card

I am looking for a new company business card. Front and back. With information on it as per below. Card should be professional. Yet clever. Simple. Modern design. Pim card, traditional size. OK with say, all black or all red backside.

Varnholt is an indie, bootstrapped magazine advancing the work of intersectional feminists busting their buts to create a just world through the power of enterprise and innovation.

Varnholt is the home and voice of entrepreneurial feminism and feminist innovators worldwide. Entrepreneurial feminists are people (of all genders) who see inequality as an innovation priority. They work to advance gender equity and/or who strive to integrate and practice feminist principles, pedagogy, values into their innovation and entrepreneurship work.
We are committed to this space being trans and queer inclusive, anti-racist, intersectional, brave, and safe. We welcome all allies. We value learning, edgy but civil discourse and integrative thinking skills.

Target Market(s)

feminists, business owners,

Industry/Entity Type

Publishing Company

Contact Information for Business Card

RD Tolliver
Founder/Publisher
4-237 Ashgrove Lane, Toronto, ON
M4T 2K8
publisher@varnholt.com
416-552-3019
www.varnholt.com

Font styles to use
Serif
Other font styles liked:
• Myriad Pro

Colors
ec1f27
000000
ffffff

Requirements
Must have
• logo
• use red, black white colours only.
Nice to have
• use the compass in pattern or creatively but not too busy please
Should not have
• Should not be too busy. Elegant.

```html
<!DOCTYPE html>
<html lang="en">
<head>
<meta charset="utf-8">
<title>Varnholt business card</title>
<link rel="stylesheet" href="https://fonts.googleapis.com/css2?family=Open+Sans:wght@400;600;800&display=swap">
<style>
  :root {
    --page: #ececec;
    --paper: #f4f4f4;
    --ink: #1b1b1b;
    --ink-soft: #3a3a3a;
    --night: #2b2b2b;
    --red: #ec1f27;
    --white: #ffffff;
  }
  * { box-sizing: border-box; margin: 0; padding: 0; }
  html, body {
    width: 1200px; height: 1184px; overflow: hidden;
    background: var(--page);
    font-family: "Open Sans", sans-serif;
  }
  .card {
    position: absolute; left: 150px;
    width: 900px; height: 514px;
    box-shadow: 0 6px 18px rgba(0,0,0,.12);
  }
  .card-front { top: 48px; background: var(--paper); }
  .card-back { top: 622px; background: var(--night); overflow: hidden; }

  .frame {
    position: absolute; inset: 26px;
    border: 1.5px solid var(--ink);
  }
  .brand {
    position: absolute; left: 80px; top: 200px;
    display: flex; align-items: center; gap: 16px;
  }
  .brand-name {
    font-weight: 800; font-size: 70px; letter-spacing: -1px;
    color: var(--ink); line-height: 1;
  }
  .brand-dot {
    width: 22px; height: 22px; border-radius: 50%;
    border: 2px solid var(--ink);
  }
  .divider {
    position: absolute; left: 470px; top: 150px;
    width: 1.5px; height: 214px; background: #9a9a9a;
  }
  .contact {
    position: absolute; left: 510px; top: 140px;
    color: var(--ink-soft); font-size: 22px; line-height: 1.35;
  }
  .contact-name { font-weight: 800; font-size: 30px; color: var(--ink); }
  .contact-role { margin-bottom: 6px; }
  .contact-lines { list-style: none; margin-top: 6px; }
  .contact-lines li { display: flex; align-items: center; gap: 12px; }
  .contact-lines svg { width: 20px; height: 20px; flex: none; }

  .artwork {
    position: absolute; left: 110px; top: 30px;
    width: 680px; height: 400px; border-radius: 50%;
    background: radial-gradient(ellipse at center, #3d3d3d 0%, #333 55%, var(--night) 100%);
  }
  .brand-back {
    position: absolute; right: 70px; bottom: 52px;
    display: flex; align-items: center; gap: 14px;
  }
  .brand-back .brand-name { color: var(--white); font-size: 64px; }
  .brand-back .brand-dot { border-color: var(--white); }
</style>
</head>
<body>
  <section class="card card-front">
    <div class="frame"></div>
    <div class="brand">
      <span class="brand-name">Varnholt</span>
      <span class="brand-dot"></span>
    </div>
    <div class="divider"></div>
    <div class="contact">
      <p class="contact-name">RD Tolliver</p>
      <p class="contact-role">Founder/Publisher</p>
      <p>4-237 Ashgrove Lane</p>
      <p>Toronto, ON, M4T 2K8</p>
      <ul class="contact-lines">
        <li>
          <svg viewBox="0 0 20 20" aria-hidden="true"><path d="M6 2 L9 6 L7 8 Q9 12 12 13 L14 11 L18 14 L16 18 Q6 17 2 5 Z" fill="none" stroke="#ec1f27" stroke-width="1.8"/></svg>
          416-552-3019
        </li>
        <li>
          <svg viewBox="0 0 20 20" aria-hidden="true"><rect x="2" y="4" width="16" height="12" fill="none" stroke="#ec1f27" stroke-width="1.8"/><path d="M2 4 L10 11 L18 4" fill="none" stroke="#ec1f27" stroke-width="1.8"/></svg>
          publisher@varnholt.com
        </li>
        <li>
          <svg viewBox="0 0 20 20" aria-hidden="true"><circle cx="10" cy="10" r="8" fill="none" stroke="#ec1f27" stroke-width="1.8"/><path d="M2 10 H18 M10 2 V18 M4 5.5 H16 M4 14.5 H16" fill="none" stroke="#ec1f27" stroke-width="1.4"/></svg>
          www.varnholt.com
        </li>
      </ul>
    </div>
  </section>

  <section class="card card-back">
    <div class="artwork" role="img" aria-label="Line illustration of a crowd of diverse women with small hearts and symbols, drawn in grey on black"></div>
    <div class="brand-back">
      <span class="brand-name">Varnholt</span>
      <span class="brand-dot"></span>
    </div>
  </section>
</body>
</html>
```